Young, dynamic furniture company needs a new business card design

We require a new business card design for our modern furniture company which supplies furniture and appliances to the property and development market.
Oakridge Interiors has become one of the leading furniture & appliance suppliers to the property market withing London. With over 10 years experience, we have increased our business to supply not only private landlords and managing agents, but also property developers, housing associations and local councils.
We offer not only a complete range of furniture which includes beds, wardrobes, dining sets and sofas, but also a high quality, full delivery and assembly service to help you with all our furnishing needs.

Target Market(s)

Private landlords, estate agents, letting agents, property management companies

Industry/Entity Type

Business

Contact Information for Business Card

Name,
Title,
Address,
Mobile,
Telephone,
Fax, Website, email address

Font styles to use
Sans Serif

Colors
3176b5
0555a3
85abd2
cfdeed

Requirements
Must have
• All the above information for each of our staff, along with our logo

```html
<!DOCTYPE html>
<html lang="en">
<head>
<meta charset="utf-8">
<title>Oakridge Interiors – Business Card</title>
<link href="https://fonts.googleapis.com/css2?family=Lato:wght@400;700&display=swap" rel="stylesheet">
<style>
  :root {
    --blue-mid: #3176b5;
    --blue-deep: #0555a3;
    --blue-light: #85abd2;
    --blue-pale: #cfdeed;
    --ink: #111418;
    --paper: #ffffff;
    --backdrop: #3a3c40;
  }
  * { margin: 0; padding: 0; box-sizing: border-box; }
  html, body { width: 1200px; height: 900px; overflow: hidden; }
  body {
    background: var(--backdrop);
    font-family: "Lato", Arial, sans-serif;
    position: relative;
  }
  .card {
    position: absolute;
    width: 620px;
    height: 380px;
    overflow: hidden;
    box-shadow: 0 10px 28px rgba(0,0,0,0.45);
  }

  /* Back of card */
  .card-back {
    left: 530px;
    top: 50px;
    background: var(--blue-deep);
    color: var(--paper);
    text-align: center;
  }
  .card-back .brand {
    margin-top: 120px;
    display: flex;
    justify-content: center;
    align-items: center;
    gap: 14px;
  }
  .card-back .brand-mark {
    width: 26px; height: 26px;
    background: var(--paper);
  }
  .card-back .brand-name {
    font-size: 36px;
    font-weight: 400;
    letter-spacing: 1px;
    text-transform: uppercase;
  }
  .card-back .tagline {
    margin-top: 6px;
    font-size: 15px;
    letter-spacing: 1.5px;
    text-transform: uppercase;
  }
  .card-back .website {
    margin-top: 34px;
    font-size: 17px;
    letter-spacing: 2.5px;
  }

  /* Front of card */
  .card-front {
    left: 50px;
    top: 480px;
    background: var(--paper);
    color: var(--ink);
  }
  .card-front .sweep {
    position: absolute;
    inset: 0;
  }
  .card-front .brand {
    position: absolute;
    left: 44px;
    top: 40px;
    display: flex;
    align-items: center;
    gap: 10px;
  }
  .card-front .brand-mark {
    width: 18px; height: 18px;
    background: var(--blue-deep);
  }
  .card-front .brand-name {
    font-size: 24px;
    text-transform: uppercase;
    letter-spacing: 0.5px;
    color: var(--ink);
  }
  .card-front .tagline {
    position: absolute;
    left: 72px;
    top: 72px;
    font-size: 10px;
    letter-spacing: 1px;
    text-transform: uppercase;
    color: var(--ink);
  }
  .card-front .person {
    position: absolute;
    left: 44px;
    top: 118px;
  }
  .person .name { font-size: 26px; font-weight: 400; }
  .person .role { font-size: 16px; color: var(--blue-mid); margin-top: 2px; }
  .person .address { font-size: 16px; line-height: 1.35; margin-top: 18px; }

  .contacts {
    position: absolute;
    left: 250px;
    top: 262px;
    list-style: none;
    font-size: 17px;
    line-height: 24px;
  }
  .contacts li { display: flex; align-items: center; gap: 12px; }
  .contacts svg { width: 14px; height: 14px; fill: var(--blue-mid); flex: none; }
</style>
</head>
<body>

  <section class="card card-back">
    <div class="brand">
      <span class="brand-mark"></span>
      <span class="brand-name">Oakridge Interiors</span>
    </div>
    <p class="tagline">Trade Furniture Solutions</p>
    <p class="website">www.trade.oakridgeint.co.uk</p>
  </section>

  <section class="card card-front">
    <svg class="sweep" viewBox="0 0 620 380" preserveAspectRatio="none">
      <path d="M250 0 C450 40 565 200 545 380 L620 380 L620 0 Z" fill="var(--blue-light)"/>
      <path d="M300 0 C495 50 590 210 570 380 L620 380 L620 0 Z" fill="var(--blue-mid)" stroke="var(--paper)" stroke-width="4"/>
    </svg>

    <div class="brand">
      <span class="brand-mark"></span>
      <span class="brand-name">Oakridge Interiors</span>
    </div>
    <p class="tagline">Trade Furniture Solutions</p>

    <div class="person">
      <p class="name">Daniel Hartley</p>
      <p class="role">Manager</p>
      <p class="address">27B Fernlow Trade Estate<br>Westbrook, London</p>
    </div>

    <ul class="contacts">
      <li>
        <svg viewBox="0 0 16 16"><path d="M3.5 1 L6 1 L7 5 L5.3 6.3 C6.2 8.3 7.7 9.8 9.7 10.7 L11 9 L15 10 L15 12.5 C15 14 13.8 15 12.5 15 C6.2 15 1 9.8 1 3.5 C1 2.2 2 1 3.5 1 Z"/></svg>
        020 7946 0321
      </li>
      <li>
        <svg viewBox="0 0 16 16"><path d="M4 0 H12 A1 1 0 0 1 13 1 V15 A1 1 0 0 1 12 16 H4 A1 1 0 0 1 3 15 V1 A1 1 0 0 1 4 0 Z M5 2 V11 H11 V2 Z M7 13 H9 V14 H7 Z"/></svg>
        020 7946 0000
      </li>
      <li>
        <svg viewBox="0 0 16 16"><path d="M1 3 H15 V13 H1 Z M2 4 L8 9 L14 4 Z"/></svg>
        info@trade.oakridgeint.co.uk
      </li>
      <li>
        <svg viewBox="0 0 16 16"><circle cx="8" cy="8" r="7"/><path d="M1 8 H15 M8 1 C4.5 4.5 4.5 11.5 8 15 M8 1 C11.5 4.5 11.5 11.5 8 15" stroke="#fff" stroke-width="1" fill="none"/></svg>
        www.trade.oakridgeint.co.uk
      </li>
    </ul>
  </section>

</body>
</html>
```